Business Card Design

We need a business card designed for our new company. Prefer a black card with white logo & writing.

Contact Information for Business Card

Ted Galloway, address: 7-4812 Fernhollow Road, Abbotsford, BC, V3K 8R2, Office Phone: 604-712-3390, Cell: 604-947-2164, Email: ted@resinworkshub.ca

Colors

Designer to choose only greyscale colors for use in the design.

```html
<!DOCTYPE html>
<html lang="en">
<head>
<meta charset="utf-8">
<title>Resin Works Hub – Business Card</title>
<link rel="stylesheet" href="https://fonts.googleapis.com/css2?family=Poppins:wght@400;700&family=Arimo:wght@400;700&display=swap">
<style>
  :root {
    --backdrop: #a3a3a3;
    --card-dark: #343336;
    --card-panel: #545556;
    --band-light: #dcdcdc;
    --ink-white: #ffffff;
    --ink-soft: #d6d6d6;
    --ink-dark: #222222;
  }
  * { margin: 0; padding: 0; box-sizing: border-box; }
  html, body {
    width: 1200px; height: 900px; overflow: hidden;
    background: var(--backdrop);
  }
  .canvas { position: relative; width: 1200px; height: 900px; }
  .card {
    position: absolute; top: 287px;
    width: 540px; height: 327px;
    background: var(--card-dark);
    overflow: hidden;
  }
  .card--front { left: 40px; }
  .card--back { left: 620px; }

  .brand-name {
    position: absolute;
    transform: translate(-50%, -50%);
    font-family: "Poppins", sans-serif;
    font-weight: 700;
    font-size: 17px;
    letter-spacing: 0.04em;
    color: var(--ink-white);
    white-space: nowrap;
  }

  /* front */
  .front-panel {
    position: absolute; left: 121px; top: 0;
    width: 299px; height: 293px;
    background: var(--card-panel);
  }
  .front-band {
    position: absolute; left: 0; top: 239px;
    width: 540px; height: 33px;
    background: var(--band-light);
    display: flex; align-items: center; justify-content: center;
  }
  .web-address {
    font-family: "Arimo", sans-serif;
    font-weight: 700;
    font-size: 12px;
    letter-spacing: 0.25em;
    color: var(--ink-dark);
  }
  .card--front .brand-name { left: 270px; top: 132px; }

  /* back */
  .back-panel {
    position: absolute; left: 226px; top: 55px;
    width: 314px; height: 217px;
    background: var(--card-panel);
  }
  .back-strip {
    position: absolute; left: 245px; top: 0;
    width: 33px; height: 121px;
    background: var(--band-light);
  }
  .card--back .brand-name { left: 114px; top: 163px; }
  .holder-name {
    position: absolute; left: 296px; top: 84px;
    font-family: "Poppins", sans-serif;
    font-size: 21px;
    letter-spacing: 0.05em;
    color: var(--ink-soft);
    white-space: nowrap;
  }
  .holder-name .first { font-weight: 700; color: var(--ink-white); }
  .holder-name .last { font-weight: 400; }
  .contact-icon {
    position: absolute; left: 245px;
    width: 33px; height: 33px;
    border: 2px solid var(--ink-white);
    display: flex; align-items: center; justify-content: center;
  }
  .contact-icon svg { width: 17px; height: 17px; fill: var(--ink-soft); }
  .icon-phone { top: 142px; }
  .icon-mail { top: 182px; }
  .icon-pin { top: 222px; }
  .contact-text {
    position: absolute; left: 296px;
    font-family: "Arimo", sans-serif;
    font-size: 11.5px;
    line-height: 16px;
    color: var(--ink-white);
    white-space: nowrap;
  }
  .text-phone { top: 142px; }
  .text-mail { top: 189px; }
  .text-address { top: 223px; }
</style>
</head>
<body>
<main class="canvas">

  <section class="card card--front" aria-label="Business card front">
    <div class="front-panel"></div>
    <div class="brand-name">RESIN WORKS HUB</div>
    <div class="front-band"><span class="web-address">www.resinworkshub.shop</span></div>
  </section>

  <section class="card card--back" aria-label="Business card back">
    <div class="back-panel"></div>
    <div class="back-strip"></div>
    <div class="brand-name">RESIN WORKS HUB</div>

    <h1 class="holder-name"><span class="first">TED</span> <span class="last">GALLOWAY</span></h1>

    <div class="contact-icon icon-phone">
      <svg viewBox="0 0 24 24" aria-hidden="true"><path d="M6.6 10.8c1.4 2.8 3.8 5.1 6.6 6.6l2.2-2.2c.3-.3.7-.4 1-.2 1.1.4 2.3.6 3.6.6.6 0 1 .4 1 1V20c0 .6-.4 1-1 1C10.6 21 3 13.4 3 4c0-.6.4-1 1-1h3.5c.6 0 1 .4 1 1 0 1.3.2 2.5.6 3.6.1.3 0 .7-.2 1z"/></svg>
    </div>
    <p class="contact-text text-phone">604-712-3390 (Office)<br>604-947-2164 (Cell)</p>

    <div class="contact-icon icon-mail">
      <svg viewBox="0 0 24 24" aria-hidden="true"><path d="M3 6h18v12H3z" fill="none"/><path d="M3 6l9 6 9-6v12H3z"/><path d="M3 5h18l-9 6z"/></svg>
    </div>
    <p class="contact-text text-mail">ted@resinworkshub.ca</p>

    <div class="contact-icon icon-pin">
      <svg viewBox="0 0 24 24" aria-hidden="true"><path d="M12 2a7 7 0 0 0-7 7c0 5 7 13 7 13s7-8 7-13a7 7 0 0 0-7-7zm0 9.5A2.5 2.5 0 1 1 12 6.5a2.5 2.5 0 0 1 0 5z"/></svg>
    </div>
    <p class="contact-text text-address">7-4812 Fernhollow Road,<br>Abbotsford, BC, V3K 8R2</p>
  </section>

</main>
</body>
</html>
```